KBT Business Cards

We require business cards for our business. We would like a matte black back to the card, with our logo centred in the middle. The front side of the card is open to design.

Target Market(s)

Clients looking for legal services (professional)

Industry/Entity Type

Legal

Contact Information for Business Card

Doran Kelbrath
Partner
Mobile: 0461 738 524
Email: doran@kbtlaw.co
Website: www.kbtlaw.co
Level 3, 118 Wendmore Street
Sydney NSW 2000

Font styles to use
Other font styles liked:
• Avenir

Colors
f04a50
ffffff
1b1b1b

Requirements
Must have
• Black back with logo included in the centre of the card.
• Our font is Avenir.

```html
<!DOCTYPE html>
<html lang="en">
<head>
<meta charset="utf-8">
<title>KBT Legal Business Cards</title>
<link href="https://fonts.googleapis.com/css2?family=Nunito+Sans:wght@400;600;700;800&display=swap" rel="stylesheet">
<style>
  :root {
    --stage: #2b2b2b;
    --accent: #f04a50;
    --ink: #1b1b1b;
    --matte: #1b1b1b;
    --matte-light: #262626;
    --paper: #ffffff;
    --rule: #3a3a3a;
  }
  * { margin: 0; padding: 0; box-sizing: border-box; }
  html, body {
    width: 1200px; height: 900px; overflow: hidden;
    background: var(--stage);
    font-family: "Nunito Sans", "Avenir", sans-serif;
  }
  .card {
    position: absolute; left: 290px; width: 620px; height: 378px;
    overflow: hidden; box-shadow: 0 12px 30px rgba(0,0,0,.45);
  }

  /* Back of card: matte black */
  .card-back { top: 48px; background: var(--matte); }
  .back-texture {
    position: absolute; inset: 0;
    background:
      radial-gradient(ellipse at 25% 20%, rgba(255,255,255,.05), transparent 60%),
      linear-gradient(160deg, var(--matte-light) 0%, var(--matte) 55%, #141414 100%);
  }
  .brand { position: absolute; display: flex; align-items: center; gap: 18px; }
  .brand-mark { width: 46px; height: 46px; flex: none; }
  .brand-name { font-weight: 800; font-size: 40px; letter-spacing: 1px; line-height: 1; }
  .card-back .brand { left: 50%; top: 50%; transform: translate(-50%, -50%); }
  .card-back .brand-mark { background: var(--accent); }
  .card-back .brand-name { color: var(--paper); }

  /* Front of card */
  .card-front { top: 472px; background: var(--paper); }
  .person { position: absolute; left: 40px; top: 92px; }
  .person-name {
    color: var(--accent); font-weight: 800; font-size: 25px;
    letter-spacing: .5px; line-height: 1; text-transform: uppercase;
  }
  .person-role { color: var(--ink); font-size: 15px; margin-top: 6px; }
  .card-front .brand { right: 40px; top: 92px; gap: 14px; }
  .card-front .brand-mark { width: 40px; height: 40px; background: var(--accent); }
  .card-front .brand-name { color: var(--ink); font-size: 36px; }
  .divider {
    position: absolute; left: 40px; right: 40px; top: 182px;
    height: 1px; background: var(--rule);
  }
  .contact { position: absolute; left: 40px; top: 204px; list-style: none; }
  .contact li {
    display: flex; align-items: center; gap: 12px;
    color: var(--ink); font-size: 16px; height: 26px;
  }
  .contact svg { width: 16px; height: 16px; fill: var(--accent); flex: none; }
  .address {
    position: absolute; right: 40px; top: 226px;
    text-align: right; color: var(--ink); font-size: 16px; line-height: 1.5;
    font-style: normal;
  }
  .bands { position: absolute; left: 0; top: 0; width: 620px; height: 378px; }
  .website {
    position: absolute; right: 40px; bottom: 20px;
    color: var(--paper); font-size: 17px; font-weight: 600; letter-spacing: 2px;
  }
</style>
</head>
<body>
  <section class="card card-back" aria-label="Back of card">
    <div class="back-texture" role="img" aria-label="Subtle matte black diamond pattern"></div>
    <div class="brand">
      <span class="brand-mark"></span>
      <span class="brand-name">KBT LEGAL</span>
    </div>
  </section>

  <section class="card card-front" aria-label="Front of card">
    <svg class="bands" viewBox="0 0 620 378" aria-hidden="true">
      <polygon points="0,270 292,270 282,281 0,281" fill="#1b1b1b"/>
      <polygon points="0,290 270,290 288,310 620,310 620,378 0,378" fill="#f04a50"/>
    </svg>

    <div class="person">
      <div class="person-name">Doran Kelbrath</div>
      <div class="person-role">Partner</div>
    </div>

    <div class="brand">
      <span class="brand-mark"></span>
      <span class="brand-name">KBT LEGAL</span>
    </div>

    <div class="divider"></div>

    <ul class="contact">
      <li>
        <svg viewBox="0 0 24 24"><path d="M6.6 10.8a15.1 15.1 0 0 0 6.6 6.6l2.2-2.2a1 1 0 0 1 1-.25 11.4 11.4 0 0 0 3.6.57 1 1 0 0 1 1 1V20a1 1 0 0 1-1 1A17 17 0 0 1 3 4a1 1 0 0 1 1-1h3.5a1 1 0 0 1 1 1c0 1.25.2 2.45.57 3.57a1 1 0 0 1-.25 1z"/></svg>
        0461 738 524
      </li>
      <li>
        <svg viewBox="0 0 24 24"><path d="M2 5h20v14H2z M3.5 6.5 12 13l8.5-6.5" stroke="#fff" stroke-width="1.4"/></svg>
        doran@kbtlaw.co
      </li>
    </ul>

    <address class="address">
      Level 3, 118 Wendmore Street<br>
      Sydney NSW 2000
    </address>

    <div class="website">www.kbtlaw.co</div>
  </section>
</body>
</html>
```